Design the packaging for a wholesale/retail Date fruit company

We need a box designed for a dates fruit box. This will be used for the wholesale packaging. The brand is called Zahwan Dates , it is a new business. Zahwan means the home. It will be part of a food exporting business called Zahwan Foods. It will be based out of the Middle East and the Holy Lands. Recently Qatar had a desert games and one of their stadiums was also called Zahwan, it was designed to represent an Arabian tent. The logo hasn't been designed yet but something simple is fine. I also have a sample design, you can use most of the information from. The product is a Product of Palestine, it is in 5kg boxes the nutritional information is on the sample.

The company is called Hadi Nasrallah General Trading (HNGT) based in Doha Qatar. Logo is provided.

The exporter details are on the sample box.
Use this companies packaging as inspiration for what we are looking to compete with https://morvane-example.com/

I require the illustrator/photoshop files please so that we can update details on it.

Industry/Entity Type

food (dates)

Requirements
Must have
• English & Arabic text
Nice to have
• try and incorporate the colour CFB53B

```html
<!DOCTYPE html>
<html lang="en">
<head>
<meta charset="utf-8">
<title>Zahwan Dates – Wholesale Box Dieline</title>
<link rel="stylesheet" href="https://fonts.googleapis.com/css2?family=Montserrat:wght@400;500&family=Cormorant+Garamond:wght@500&family=Tajawal:wght@400;500&display=swap">
<style>
  :root {
    --paper: #ffffff;
    --cut: #3a55b8;
    --fold: #d9534f;
    --crease: #9b4fb5;
    --glue: #e6e04a;
    --teal-deep: #072a2c;
    --teal: #0f6b6a;
    --teal-light: #1b8b88;
    --gold: #cfb53b;
    --brand: #8c6d1f;
    --text-light: #ffffff;
  }
  html, body {
    margin: 0;
    padding: 0;
    width: 1200px;
    height: 1200px;
    overflow: hidden;
    background: var(--paper);
  }
  .dieline {
    position: absolute;
    left: 45px;
    top: 138px;
    width: 1110px;
    height: 924px;
  }
  .cut-line { fill: none; stroke: var(--cut); stroke-width: 1.4; }
  .fold-line { fill: none; stroke: var(--fold); stroke-width: 1.2; }
  .crease-line { fill: none; stroke: var(--crease); stroke-width: 1.2; }
  .glue-hatch { stroke: var(--glue); stroke-width: 1.3; }
  .brand-name-ar {
    font-family: "Tajawal", serif;
    font-weight: 500;
    fill: var(--brand);
  }
  .brand-name {
    font-family: "Cormorant Garamond", "Tajawal", serif;
    font-weight: 500;
    fill: var(--brand);
  }
  .label-ar {
    font-family: "Tajawal", sans-serif;
    font-weight: 400;
    fill: var(--text-light);
  }
  .label-en {
    font-family: "Montserrat", sans-serif;
    font-weight: 400;
    fill: var(--text-light);
  }
  .divider { stroke: var(--gold); stroke-width: 2; }
</style>
</head>
<body>
<svg class="dieline" viewBox="370 950 1192 992" xmlns="http://www.w3.org/2000/svg">
  <defs>
    <radialGradient id="cityTones" cx="45%" cy="55%" r="65%">
      <stop offset="0%" stop-color="#d9a53a"/>
      <stop offset="35%" stop-color="#b98a62"/>
      <stop offset="70%" stop-color="#8a7a68"/>
      <stop offset="100%" stop-color="#c9c4bd" stop-opacity="0"/>
    </radialGradient>
    <radialGradient id="dateTones" cx="50%" cy="50%" r="55%">
      <stop offset="0%" stop-color="#6e1f1a"/>
      <stop offset="70%" stop-color="#4a1410"/>
      <stop offset="100%" stop-color="#ffffff" stop-opacity="0"/>
    </radialGradient>
    <radialGradient id="tealGlow" cx="50%" cy="65%" r="70%">
      <stop offset="0%" stop-color="var(--teal-light)"/>
      <stop offset="100%" stop-color="var(--teal-deep)"/>
    </radialGradient>
    <linearGradient id="stripShade" x1="0" x2="1">
      <stop offset="0%" stop-color="#dfe6e6"/>
      <stop offset="8%" stop-color="#ffffff"/>
      <stop offset="92%" stop-color="#ffffff"/>
      <stop offset="100%" stop-color="#dfe6e6"/>
    </linearGradient>
    <filter id="soften" x="-10%" y="-10%" width="120%" height="120%">
      <feGaussianBlur stdDeviation="10"/>
    </filter>
  </defs>

  <!-- glue tabs -->
  <g class="glue-tabs">
    <path class="cut-line" d="M388 974 H510 L552 1137 H388 Z"/>
    <path class="cut-line" d="M1422 974 H1544 V1137 H1380 Z"/>
    <path class="cut-line" d="M388 1757 H552 L510 1930 H388 Z"/>
    <path class="cut-line" d="M1380 1757 H1544 V1930 H1422 Z"/>
    <g class="glue-hatch">
      <line x1="410" y1="1040" x2="452" y2="998"/><line x1="410" y1="1080" x2="490" y2="1000"/>
      <line x1="428" y1="1110" x2="500" y2="1038"/><line x1="470" y1="1110" x2="512" y2="1068"/>
      <line x1="1480" y1="998" x2="1522" y2="1040"/><line x1="1442" y1="1000" x2="1522" y2="1080"/>
      <line x1="1428" y1="1040" x2="1500" y2="1112"/><line x1="1418" y1="1075" x2="1458" y2="1115"/>
      <line x1="410" y1="1870" x2="490" y2="1790"/><line x1="430" y1="1900" x2="515" y2="1815"/>
      <line x1="1420" y1="1830" x2="1465" y2="1785"/><line x1="1430" y1="1880" x2="1520" y2="1790"/>
      <line x1="1470" y1="1900" x2="1522" y2="1848"/>
    </g>
  </g>

  <!-- lid flaps -->
  <g class="flaps">
    <path class="cut-line" d="M556 1137 V962 H1372 V1137"/>
    <path class="cut-line" d="M556 1755 V1930 H1372 V1755"/>
    <line class="crease-line" x1="732" y1="962" x2="566" y2="1122"/>
    <line class="crease-line" x1="1200" y1="962" x2="1366" y2="1122"/>
    <line class="crease-line" x1="566" y1="1770" x2="732" y2="1930"/>
    <line class="crease-line" x1="1366" y1="1770" x2="1200" y2="1930"/>
  </g>

  <!-- side walls -->
  <g class="side-walls">
    <path class="cut-line" d="M380 1137 V1418 A28 28 0 0 1 380 1474 V1755"/>
    <path class="cut-line" d="M1552 1137 V1418 A28 28 0 0 0 1552 1474 V1755"/>
    <line class="fold-line" x1="380" y1="1137" x2="1552" y2="1137"/>
    <line class="fold-line" x1="380" y1="1755" x2="1552" y2="1755"/>
    <line class="fold-line" x1="556" y1="1137" x2="556" y2="1755"/>
    <line class="fold-line" x1="1377" y1="1137" x2="1377" y2="1755"/>
  </g>

  <!-- lid artwork -->
  <g class="lid-artwork">
    <path class="city-painting" role="img"
          aria-label="Watercolour painting of the Old City of Jerusalem with the golden Dome of the Rock"
          fill="url(#cityTones)" filter="url(#soften)"
          d="M560 1260 C600 1200 700 1190 800 1200 C900 1180 1020 1190 1075 1230 C1090 1330 1060 1420 1080 1500 C1040 1560 960 1600 880 1630 C780 1650 660 1640 560 1620 Z"/>

    <path class="dates-photo" role="img" aria-label="Photograph of three glossy Medjool dates"
          fill="url(#dateTones)" filter="url(#soften)"
          d="M910 1610 C960 1560 1060 1540 1150 1545 C1210 1560 1230 1640 1215 1700 C1190 1740 1100 1750 1050 1720 C1000 1680 930 1670 910 1640 Z"/>

    <!-- brand ribbon -->
    <g class="brand-ribbon">
      <path fill="url(#stripShade)"
            d="M592 1040 H762 V1262 C740 1262 725 1275 712 1285 C700 1290 690 1300 677 1305 C664 1300 654 1290 642 1285 C629 1275 614 1262 592 1262 Z"/>
      <text class="brand-name-ar" x="677" y="1205" text-anchor="middle" font-size="40" direction="rtl">تمور زهوان</text>
      <text class="brand-name" x="677" y="1250" text-anchor="middle" font-size="24">Zahwan Dates</text>
    </g>

    <!-- product label -->
    <g class="product-label">
      <path fill="none" stroke="var(--gold)" stroke-width="2"
            d="M1117 1230 C1150 1225 1185 1210 1215 1185 C1245 1210 1280 1225 1313 1230 V1490 C1280 1495 1245 1520 1215 1545 C1185 1520 1150 1495 1117 1490 Z"/>
      <path fill="url(#tealGlow)"
            d="M1126 1240 C1158 1235 1190 1220 1215 1198 C1240 1220 1272 1235 1304 1240 V1482 C1272 1488 1240 1510 1215 1532 C1190 1510 1158 1488 1126 1482 Z"/>
      <text class="label-ar" x="1212" y="1292" text-anchor="middle" font-size="36">تمر مجول</text>
      <text class="label-ar" x="1212" y="1330" text-anchor="middle" font-size="34">فلسطيني</text>
      <text class="label-en" x="1212" y="1362" text-anchor="middle" font-size="36">Medjool</text>
      <text class="label-en" x="1212" y="1405" text-anchor="middle" font-size="48">Dates</text>
      <line class="divider" x1="1140" y1="1433" x2="1290" y2="1433"/>
      <text class="label-en" x="1214" y="1462" text-anchor="middle" font-size="18">Natural</text>
      <text class="label-en" x="1214" y="1480" text-anchor="middle" font-size="18">Sweetness</text>
    </g>

    <!-- net weight tag -->
    <g class="weight-tag">
      <path fill="url(#tealGlow)"
            d="M567 1652 C600 1650 640 1640 660 1612 C680 1640 720 1650 803 1652 V1830 C790 1830 780 1836 775 1845 H595 C590 1836 580 1830 567 1830 Z"/>
      <text class="label-en" x="677" y="1700" font-size="24">5 Kg/</text>
      <text class="label-en" x="677" y="1722" font-size="20">11LBS NET</text>
    </g>
  </g>
</svg>
</body>
</html>
```